A New and modern Business Card for Tarwick Trade Solutions Ltd

New and modern Logo and Business Card Attached is the current logo/business card designCurrently the business is called "Tarwick & Co." or TTS Ltd for short. This is subject to change.This business specialises in Telecoms and Energy. We work with the major networks (QV, K7, etc) and also offer Energy Products saving clients money off their energy bills.These are business to business services.The current design incorporates a Pheonix, indicating rebirth, starting something new.We would like to maintain the Phoenix element but a newer modern style.We love colours in the logo 3 max.The aim of this is to be ultra slick and modern. I envisage Tarwick & Co. on one side of the card with long descriptions on the other side.Side 1:TTS Ltd/Logo?Side 2:TTS Ltd/Logo/Graphic?Brogan & Co.Name:Address:Phone:Email:The design is mostly flexible but must incorporate a Phoenix.For example "Tarwick & Co." with a block phoenix behind the text...up to you.

Industry/Entity Type

Telecommunications

Contact Information for Business Card

Tarwick & Co.
Address:
Name:
Phone:
Email:

Logo Text

Tarwick & Co.

Colors
33a6d7
0792cd
acd037
9bcb3c
f78f20
fece3e

Requirements
Must have
• Phoenix
• 3/4 colours max
• Blue representing Technology (wireless)
• Green for Eco Energy
• Orange for Phoenix
• White business card background
Should not have
• phoenix must not all be red/ orange fire, we are a technology service company and the phoenix colours must represent this. Fire is not representative of our company.

```html
<!DOCTYPE html>
<html lang="en">
<head>
<meta charset="utf-8">
<title>Tarwick Trade Solutions Ltd – Business Card</title>
<link href="https://fonts.googleapis.com/css2?family=Lato:wght@400;700&display=swap" rel="stylesheet">
<style>
  :root {
    --stage: #5b5b5b;
    --card-white: #ffffff;
    --tech-blue: #0792cd;
    --tech-blue-light: #33a6d7;
    --eco-green: #9bcb3c;
    --phoenix-orange: #f78f20;
    --ink: #2b2b2b;
    --divider: #8a8a8a;
  }
  * { margin: 0; padding: 0; box-sizing: border-box; }
  html, body { width: 1200px; height: 802px; overflow: hidden; }
  body {
    background: var(--stage);
    font-family: "Lato", sans-serif;
    position: relative;
  }
  .card {
    position: absolute;
    top: 274px;
    width: 443px;
    height: 265px;
    box-shadow: 0 3px 8px rgba(0,0,0,0.35);
    overflow: hidden;
  }
  .card-front { left: 136px; background: var(--card-white); }
  .card-back {
    left: 624px;
    background: linear-gradient(135deg, var(--tech-blue-light) 0%, var(--tech-blue) 60%, #06749f 100%);
    display: flex; align-items: center; justify-content: center;
  }
  .card-back .emblem-area {
    position: absolute; inset: 0;
    background: radial-gradient(ellipse at 20% 100%, rgba(155,203,60,0.55), transparent 45%),
                radial-gradient(ellipse at 85% 0%, rgba(247,143,32,0.35), transparent 40%);
  }
  .brand-block {
    position: absolute;
    left: 36px; top: 70px;
    width: 168px;
    display: flex; flex-direction: column; align-items: center;
  }
  .brand-dot {
    width: 60px; height: 60px; border-radius: 50%;
    background: var(--phoenix-orange);
    margin-bottom: 12px;
  }
  .brand-name {
    font-weight: 700; font-size: 15px; line-height: 1.3;
    color: var(--tech-blue); text-align: center; letter-spacing: 0.6px;
    text-transform: uppercase;
  }
  .divider {
    position: absolute; left: 222px; top: 80px;
    width: 1px; height: 106px; background: var(--divider);
  }
  .contact {
    position: absolute; left: 241px; top: 79px;
    color: var(--ink); font-size: 13px; line-height: 1.25;
  }
  .contact .person {
    font-size: 16.5px; color: var(--tech-blue);
    text-transform: uppercase; letter-spacing: 0.2px;
  }
  .contact .role { margin-bottom: 9px; }
  .contact .line { display: flex; align-items: center; gap: 5px; }
  .contact .line svg { width: 10px; height: 10px; flex: none; }
  .contact .address { margin-top: 9px; }
  .back-name {
    position: relative;
    width: 380px;
    color: #fff; font-weight: 700; font-size: 27px; letter-spacing: 1.5px;
    text-transform: uppercase; text-align: center; line-height: 1.3;
  }
</style>
</head>
<body>
  <section class="card card-front">
    <div class="brand-block">
      <div class="brand-dot"></div>
      <div class="brand-name">Tarwick Trade Solutions Limited</div>
    </div>
    <div class="divider"></div>
    <div class="contact">
      <div class="person">Marcus Ellery</div>
      <div class="role">Managing Director</div>
      <div class="line">
        <svg viewBox="0 0 10 10"><path fill="#9bcb3c" d="M1 4c0-2 2-3 4-3s4 1 4 3H7V3H3v1zM2 5h6l1 4H1z"/></svg>
        044-987 654 321
      </div>
      <div class="line">
        <svg viewBox="0 0 10 10"><rect x="0.5" y="2" width="9" height="6.5" fill="#9bcb3c"/><path d="M0.5 2l4.5 3.5L9.5 2" stroke="#fff" stroke-width="0.9" fill="none"/></svg>
        info@tarwickmail.com
      </div>
      <div class="address">17, Harlow Street<br>20814, Country Name</div>
    </div>
  </section>

  <section class="card card-back">
    <div class="emblem-area" role="img" aria-label="Soft blue and green gradient where a faint large brand emblem sits"></div>
    <div class="back-name">Tarwick Trade Solutions Limited</div>
  </section>
</body>
</html>
```